Payday Lending App Interface Design

Hello, we are building a payday lending application, Lendoro, that lend people money. I have drafted some of the screens that show the functionalities we have at the moment, please find the screens in attachments.
The elements in the screens are placed just to show what should be included in those screens, it's not necessary to follow the same layout. If you have better design ideas, you are very welcomed to show off your talent.
I think what we want is a style guide so that we can apply the same style to any screens that are similar to the ones I attached. We really like
the style as in the attached image called Style.png. We might want something similar - a simple, clean design yet fun and engaging. Customised graphical elements such as icons, illustrations are preferable.
Apart from the attached screens, we might also need a design for the On Board screen and the Login/Sign Up screen too.
Our logo colour is in yellow and black. Perhaps we will have a similar colour theme. I also attached the logo file, icon-Lendoro.png, if you would like to put it in your design.
Please message me if you need further information.
Regards
Target Market(s)
Young people that doesn't have strong income

```html
<!DOCTYPE html>
<html lang="en">
<head>
<meta charset="utf-8">
<title>Lendoro – App Screens</title>
<link href="https://fonts.googleapis.com/css2?family=Roboto:wght@400;500;700&display=swap" rel="stylesheet">
<style>
  :root{
    --yellow:#fad60c;
    --yellow-deep:#f3cc05;
    --black:#0a0a0a;
    --white:#ffffff;
    --grey:#6f6f6f;
    --backdrop:#111214;
  }
  *{box-sizing:border-box;margin:0;padding:0}
  html,body{width:1200px;height:759px;overflow:hidden;background:var(--backdrop);font-family:'Roboto',sans-serif;color:var(--black)}
  .screen{position:absolute;top:95px;width:263px;height:570px;border-radius:30px;overflow:hidden}
  .screen--loan{left:111px;background:var(--yellow)}
  .screen--personal{left:469px;background:var(--yellow)}
  .screen--connect{left:826px;background:var(--white)}
  .abs{position:absolute}
  .deco{position:absolute;border-radius:50%}
  .screen-title{position:absolute;top:36px;left:0;width:100%;text-align:center;font-weight:700;font-size:14.5px;letter-spacing:.3px}
  .back{position:absolute;top:39px;left:16px;width:10px;height:14px}
  .underline{position:absolute;height:2px;left:50%;transform:translateX(-50%)}
  .underline--yellow{background:var(--yellow);width:46px}
  .underline--black{background:var(--black);width:36px}
  .section-title{position:absolute;left:0;width:100%;text-align:center;font-weight:500;font-size:14.5px;letter-spacing:.4px}

  .card{position:absolute;top:90px;left:0;width:100%;height:480px;background:var(--white);border-radius:22px 22px 0 0}
  .amount-badge{position:absolute;left:92px;top:164px;width:78px;height:78px;border-radius:50%;background:var(--yellow);display:flex;align-items:center;justify-content:center;font-weight:700;font-size:21px}
  .stat{position:absolute;top:265px;width:98px;height:38px;border-radius:5px;display:flex;align-items:center;justify-content:center;font-weight:700;font-size:13px}
  .stat--paid{left:30px;background:var(--black);color:var(--white)}
  .stat--left{left:135px;background:var(--white);box-shadow:0 2px 8px rgba(0,0,0,.12)}
  .stat-label{position:absolute;top:314px;width:98px;text-align:center;font-size:11.5px;font-weight:500;color:var(--grey)}
  .activity{position:absolute;left:32px;width:200px}
  .activity-name{font-weight:700;font-size:13px}
  .activity-date{margin-top:5px;font-size:11px;color:var(--grey);display:flex;align-items:center;gap:5px}
  .clock{width:9px;height:9px;border:1.5px solid var(--yellow);border-radius:50%}
  .activity-amount{position:absolute;right:0;top:10px;font-weight:700;font-size:13.5px}

  .intro{position:absolute;top:88px;left:0;width:100%;text-align:center;font-size:14px;line-height:20px}
  .field{position:absolute;left:15px;width:233px;height:39px;background:var(--white);border-radius:5px;padding-left:13px;display:flex;align-items:center;font-size:11.5px;color:#555}
  .field svg{position:absolute;right:12px;top:13px}
  .btn-next{position:absolute;left:15px;top:454px;width:233px;height:39px;background:var(--black);color:var(--white);border-radius:5px;display:flex;align-items:center;justify-content:center;font-weight:700;font-size:12.5px}

  .brand{position:absolute;top:170px;left:0;width:100%;display:flex;align-items:center;justify-content:center;gap:10px}
  .brand-square{width:38px;height:38px;border-radius:8px;background:var(--yellow)}
  .brand-name{font-weight:700;font-size:26px}
  .connect-title{position:absolute;top:270px;left:0;width:100%;text-align:center;font-weight:500;font-size:17px;line-height:25px;letter-spacing:.3px}
  .connect-text{position:absolute;top:348px;left:0;width:100%;text-align:center;font-size:13.5px;line-height:20px}
</style>
</head>
<body>

<section class="screen screen--loan">
  <div class="deco" style="left:120px;top:-60px;width:200px;height:200px;background:var(--yellow-deep)"></div>
  <svg class="back" viewBox="0 0 10 14"><path d="M8 1 2 7l6 6" fill="none" stroke="#0a0a0a" stroke-width="2"/></svg>
  <h1 class="screen-title">LOAN DETAILS</h1>
  <div class="card"></div>
  <h2 class="section-title" style="top:117px">NEXT REPAYMENT</h2>
  <div class="underline underline--yellow" style="top:139px"></div>
  <div class="amount-badge">$ XX</div>
  <div class="stat stat--paid">XXX</div>
  <div class="stat stat--left">XXX</div>
  <div class="stat-label" style="left:30px">Paid</div>
  <div class="stat-label" style="left:135px">Left</div>
  <h2 class="section-title" style="top:355px">ACTIVITIES</h2>
  <div class="underline underline--yellow" style="top:377px"></div>
  <div class="activity" style="top:408px">
    <div class="activity-name">REPAYMENT</div>
    <div class="activity-date"><span class="clock"></span>DD MM YY</div>
    <div class="activity-amount">$ XX</div>
  </div>
  <div class="activity" style="top:465px">
    <div class="activity-name">REPAYMENT</div>
    <div class="activity-date"><span class="clock"></span>DD MM YY</div>
    <div class="activity-amount">$ XX</div>
  </div>
</section>

<section class="screen screen--personal">
  <div class="deco" style="left:120px;top:-50px;width:200px;height:200px;background:var(--yellow-deep)"></div>
  <div class="deco" style="left:-60px;top:410px;width:200px;height:220px;background:var(--yellow-deep)"></div>
  <svg class="back" viewBox="0 0 10 14"><path d="M8 1 2 7l6 6" fill="none" stroke="#0a0a0a" stroke-width="2"/></svg>
  <h1 class="screen-title">PERSONAL DETAILS</h1>
  <p class="intro">Please provide details as<br>shown on ID</p>
  <div class="underline underline--black" style="top:135px"></div>
  <div class="field" style="top:180px">Given Name</div>
  <div class="field" style="top:229px">Middle Name</div>
  <div class="field" style="top:279px">Surname</div>
  <div class="field" style="top:328px">Date Of Birth
    <svg width="12" height="12" viewBox="0 0 12 12"><rect x="1" y="2" width="10" height="9" rx="1" fill="none" stroke="#222" stroke-width="1.3"/><path d="M1 5h10M4 1v2M8 1v2M3.5 7h1M5.5 7h1M7.5 7h1M3.5 9h1M5.5 9h1" stroke="#222" stroke-width="1.2"/></svg>
  </div>
  <div class="btn-next">NEXT</div>
</section>

<section class="screen screen--connect">
  <div class="deco" style="left:107px;top:-99px;width:240px;height:240px;background:var(--yellow)"></div>
  <div class="deco" style="left:-97px;top:428px;width:240px;height:240px;background:var(--white);box-shadow:0 0 14px rgba(250,214,12,.35)"></div>
  <div class="brand"><span class="brand-square"></span><span class="brand-name">Lendoro</span></div>
  <h1 class="connect-title">CONNECTING TO YOUR<br>BANK...</h1>
  <div class="underline underline--yellow" style="top:327px;width:30px"></div>
  <p class="connect-text">Please don't exit the app.<br>It takes 3-5 minutes to<br>confirm your details with<br>your bank</p>
</section>

</body>
</html>
```